LLC needs a business card design that emphasizes consulting and expert witness in upstream oil and g

I need a business card design for my company called Obena Consultative Service, LLC. My expertise is in oil and gas upstream operations management to optimize performance and also as an expert witness for law firms in oil and gas upstream operations litigation.
The final design should communicate knowledge and hands-on experience as well as trust. (Obena means rope or lasso. Perhaps "Obena" should be in the form of a rope.) I do not like the color green in any shade. My first preference would be some shade of blue.
Industry/Entity Type
Oil And Gas

```html
<!DOCTYPE html>
<html lang="en">
<head>
<meta charset="utf-8">
<title>Obena – Business Card</title>
<link rel="stylesheet" href="https://fonts.googleapis.com/css2?family=Arimo:wght@400;700&display=swap">
<style>
  :root {
    --navy: #1e3a7a;
    --navy-soft: #2d4b8f;
    --ink: #22367a;
    --paper: #ffffff;
    --paper-back: #f3f4f7;
    --stage: #e7e6e2;
    --ghost: rgba(30, 58, 122, 0.07);
  }
  * { box-sizing: border-box; margin: 0; padding: 0; }
  html, body { width: 1200px; height: 892px; overflow: hidden; }
  body {
    background: var(--stage);
    font-family: "Arimo", Arial, sans-serif;
    color: var(--ink);
    display: flex;
    align-items: center;
    justify-content: center;
    gap: 24px;
  }
  .card {
    position: relative;
    width: 564px;
    height: 322px;
    background: var(--paper);
    overflow: hidden;
    box-shadow: 0 6px 18px rgba(0,0,0,0.18);
  }
  .card--back { background: var(--paper-back); }
  .card__shapes { position: absolute; inset: 0; width: 100%; height: 100%; }
  .shape { fill: var(--navy); }
  .shape--soft { fill: var(--navy-soft); }

  .brand { position: absolute; display: flex; align-items: center; gap: 10px; }
  .brand__dot { border-radius: 50%; background: var(--navy); flex: none; }
  .brand__name { font-weight: 700; color: var(--navy); line-height: 1; }

  .card--front .brand { left: 26px; top: 26px; }
  .card--front .brand__dot { width: 34px; height: 34px; }
  .card--front .brand__name { font-size: 28px; }

  .person { position: absolute; left: 112px; top: 150px; }
  .person__icon { position: absolute; left: -26px; top: 2px; width: 14px; height: 14px; }
  .person__name { font-size: 24px; font-weight: 400; letter-spacing: 0.3px; }
  .person__role { font-size: 11.5px; margin-top: 2px; }

  .divider {
    position: absolute; left: 318px; top: 140px;
    width: 1px; height: 122px; background: var(--navy);
  }
  .contacts { position: absolute; left: 332px; top: 140px; list-style: none; font-size: 12px; }
  .contacts li { display: flex; align-items: flex-start; gap: 12px; margin-bottom: 6px; line-height: 1.25; }
  .contacts svg { width: 13px; height: 13px; flex: none; margin-top: 1px; fill: var(--navy); }

  .ghost-circle {
    position: absolute; left: 50%; top: 50%;
    width: 250px; height: 250px; margin: -125px 0 0 -110px;
    border-radius: 50%; border: 10px solid var(--ghost);
    background: var(--ghost);
  }
  .card--back .brand { left: 160px; top: 124px; }
  .card--back .brand__dot { width: 50px; height: 50px; }
  .card--back .brand__name { font-size: 46px; }
</style>
</head>
<body>

  <section class="card card--front" aria-label="Card front">
    <svg class="card__shapes" viewBox="0 0 564 322" preserveAspectRatio="none" aria-hidden="true">
      <polygon class="shape" points="0,110 0,322 95,322"/>
      <polygon class="shape shape--soft" points="430,0 564,0 564,150"/>
    </svg>

    <div class="brand">
      <div class="brand__dot"></div>
      <p class="brand__name">Obena</p>
    </div>

    <div class="person">
      <svg class="person__icon" viewBox="0 0 14 14" aria-hidden="true"><circle cx="7" cy="4" r="3.2" fill="var(--navy)"/><path d="M1 14c0-4 2.7-5.5 6-5.5s6 1.5 6 5.5z" fill="var(--navy)"/></svg>
      <p class="person__name">Employee name</p>
      <p class="person__role">Managing Director</p>
    </div>

    <div class="divider"></div>

    <ul class="contacts">
      <li><svg viewBox="0 0 14 14" aria-hidden="true"><path d="M3 1l2.4 2.6-1.2 1.7c.8 1.8 2.1 3.1 3.9 3.9l1.7-1.2L12.4 10.4 11 12.8C6 12.5 1.6 8 1.2 3z"/></svg>041-7306 2298</li>
      <li><svg viewBox="0 0 14 14" aria-hidden="true"><path d="M4 1h6a1 1 0 0 1 1 1v10a1 1 0 0 1-1 1H4a1 1 0 0 1-1-1V2a1 1 0 0 1 1-1zm.5 1.5v8h5v-8z"/></svg>128-4471 9032</li>
      <li><svg viewBox="0 0 14 14" aria-hidden="true"><path d="M7 0.5a4.5 4.5 0 0 1 4.5 4.5C11.5 8.5 7 13.5 7 13.5S2.5 8.5 2.5 5A4.5 4.5 0 0 1 7 .5zm0 2.7a1.8 1.8 0 1 0 0 3.6 1.8 1.8 0 0 0 0-3.6z"/></svg>Harbor Point Suite 4<br>18 Wellfield Ave Linden,<br>NJ 07036</li>
      <li><svg viewBox="0 0 14 14" aria-hidden="true"><path d="M1 2h12v8H1zm1.3 1.3v5.4h9.4V3.3zM5 11h4v1.5H5z"/></svg>www.obenaconsult.com</li>
      <li><svg viewBox="0 0 14 14" aria-hidden="true"><path d="M1 3h12v8H1zm1.2 1.1v.4L7 7.6l4.8-3.1v-.4zm0 1.8v4h9.6v-4L7 9z"/></svg>info@obenaconsult.com</li>
    </ul>
  </section>

  <section class="card card--back" aria-label="Card back">
    <svg class="card__shapes" viewBox="0 0 564 322" preserveAspectRatio="none" aria-hidden="true">
      <polygon class="shape" points="0,0 165,0 0,100"/>
      <polygon class="shape shape--soft" points="564,150 564,322 360,322"/>
    </svg>
    <div class="ghost-circle" aria-hidden="true"></div>
    <div class="brand">
      <div class="brand__dot"></div>
      <p class="brand__name">Obena</p>
    </div>
  </section>

</body>
</html>
```